Judicial election website to attract voters

I need a simple one-page web design for a judicial election. I'm going to put up one picture, maybe two. The picture I have needs a little touch-up (whiten teeth for example). I have 3 paragraphs of text. I'd like a "Donate" button that can link to a CoinDrift account. I'd also like a little background design, like the Constitution or something like that. There's a couple other little things but that's the bulk of it.

Target Market(s)

Involved voters and some media

Industry/Entity Type

Legal

Number of Pages Required

1 page

Font styles to use
Sans Serif

Requirements
Must have
• My picture, text, donate button
• Phrase "Remember to vote August 30, 2016!"
Nice to have
• Perhaps a second photo, maybe a short 30 second video of me talking directly to the voters, cool background: Constitution, something judgey.
Should not have
• Not sure ... profanity, I guess.

```html
<!DOCTYPE html>
<html lang="en">
<head>
<meta charset="utf-8">
<title>Evelyn for Judge</title>
<link href="https://fonts.googleapis.com/css2?family=Raleway:wght@400;500;600;700&family=Roboto:wght@400;500&display=swap" rel="stylesheet">
<style>
:root{
  --orange:#ee4b2b;
  --orange-soft:#f06a4a;
  --dark:#141414;
  --charcoal:#2a2a2a;
  --navy:#2f3b78;
  --light:#efefef;
  --text:#444;
  --white:#fff;
}
*{margin:0;padding:0;box-sizing:border-box}
html,body{width:1200px;height:2273px;overflow:hidden}
body{font-family:"Raleway",sans-serif;background:var(--white);position:relative;color:var(--text)}
.abs{position:absolute}

/* hero */
.hero{left:0;top:0;width:1200px;height:583px;background:linear-gradient(180deg,#3d5a9c 0%,#7d94c4 30%,#c9ccd2 55%,#6d7a5a 78%,#3f5a2c 100%)}
.topbar{left:0;top:27px;width:1200px;height:79px}
.topbar .shade{left:330px;top:0;width:870px;height:79px;background:rgba(240,240,240,.88)}
.brand{left:0;top:0;width:376px;height:79px;background:var(--orange);clip-path:polygon(0 0,100% 0,86% 100%,0 100%);display:flex;align-items:center;padding-left:100px;gap:14px}
.brand .mark{width:18px;height:18px;background:var(--white)}
.brand .name{font-family:"Roboto",sans-serif;font-weight:500;font-size:22px;color:var(--white)}
.nav{right:90px;top:0;height:79px;display:flex;align-items:center;gap:40px;font-family:"Roboto",sans-serif;font-size:16px;color:#222}
.callout{left:605px;top:224px;width:496px;height:291px;background:rgba(20,20,20,.72);text-align:right;padding:38px 18px 0 0}
.callout h1{font-family:"Roboto",sans-serif;font-weight:400;font-size:33px;line-height:58px;color:var(--white)}
.btn-vote{left:938px;top:401px;width:145px;height:51px;background:var(--orange);color:var(--white);font-family:"Roboto",sans-serif;font-size:19px;display:flex;align-items:center;justify-content:center;border-radius:4px}

/* features */
.feature{top:594px;width:389px;height:232px;color:var(--white);text-align:center;padding-top:28px}
.feature.orange{background:var(--orange-soft)}
.feature.dark{background:#1b1b1b}
.feature svg{display:block;margin:0 auto 12px}
.feature h2{font-weight:500;font-size:21px;letter-spacing:.5px;margin-bottom:10px}
.feature p{font-size:12.5px;line-height:22px;padding:0 34px}

/* about */
.portrait-frame{left:98px;top:874px;width:369px;height:461px;border:1px solid #ccc;padding:6px;background:var(--white)}
.portrait{width:100%;height:100%;background:linear-gradient(180deg,#e8e6e4 0%,#d8c2a6 45%,#e58a6a 100%)}
.about{left:504px;top:868px;width:598px}
.about h2{font-weight:500;font-size:32px;color:var(--orange);display:inline-block;border-bottom:2px solid var(--orange);padding-bottom:3px;margin-bottom:22px}
.about p{font-size:12px;line-height:24px;text-align:justify;margin-bottom:9px;color:#555}

/* vote band */
.vote-band{left:0;top:1394px;width:1200px;height:342px;background:linear-gradient(90deg,#4c5aa0 0%,#3a4688 50%,#2c3a7a 100%)}
.vote-art{left:110px;top:1410px;width:380px;height:326px;background:linear-gradient(180deg,#e9632c 0%,#9ecb3c 40%,#f1d23c 60%,#d8a784 100%);border-radius:6px;opacity:.9}
.video{left:659px;top:1430px;width:427px;height:267px;border:3px solid var(--white);background:linear-gradient(180deg,#8a8f96 0%,#4f535a 60%,#2e3036 100%)}
.video .play{left:190px;top:105px;width:38px;height:30px;background:rgba(0,0,0,.6);border-radius:4px}
.video .bar{left:16px;bottom:12px;width:390px;height:24px;background:rgba(0,0,0,.7)}
.video .track{left:8px;top:10px;width:290px;height:4px;background:#666}
.video .fill{left:0;top:0;width:125px;height:4px;background:#2aa6e0}
.video .time{left:300px;top:4px;font-size:10px;color:#ddd;font-family:"Roboto",sans-serif}

/* partners */
.partners{left:0;top:1736px;width:1200px;height:188px;background:var(--light)}
.arrow{top:82px;width:40px;height:40px;border:1.5px solid #333;border-radius:50%}
.badge{top:84px;height:34px;background:#b9b9b9;border-radius:4px}

/* cta */
.cta{left:0;top:1924px;width:1200px;height:91px;background:var(--orange)}
.cta p{left:98px;top:22px;width:560px;font-size:17px;font-weight:600;line-height:26px;color:var(--white)}
.btn-donate{left:914px;top:18px;width:172px;height:53px;background:var(--charcoal);color:var(--white);border-radius:27px;display:flex;align-items:center;justify-content:center;font-size:15px;font-weight:600;letter-spacing:.5px}

/* footer */
.footer{left:0;top:2015px;width:1200px;height:258px;background:linear-gradient(180deg,#181a1f 0%,#0d0e11 100%)}
.social{top:43px;width:44px;height:44px;border:2px solid var(--white);border-radius:50%}
.footer-nav{left:0;top:120px;width:1200px;display:flex;justify-content:center;gap:26px;font-size:14px;color:var(--white);font-weight:500}
.footer-nav .sep{opacity:.9}
.rule{left:98px;top:176px;width:1004px;height:1px;background:#444}
.copy{left:0;top:207px;width:1200px;text-align:center;font-size:14px;color:var(--white)}
</style>
</head>
<body>

<section class="hero abs" role="img" aria-label="Photograph of a white domed capitol building with columns under a blue sky, framed by trees"></section>

<header class="topbar abs">
  <div class="shade abs"></div>
  <div class="brand abs"><span class="mark"></span><span class="name">EVELYN</span></div>
  <nav class="nav abs"><span>HOME</span><span>ABOUT</span><span>EVENT</span><span>PRESS RELEASE</span><span>CONTACT</span></nav>
</header>

<div class="callout abs"><h1>" REMEMBER TO VOTE<br>AUGUST 30, 2016! "</h1></div>
<div class="btn-vote abs">VOTE ME</div>

<section class="feature orange abs" style="left:8px">
  <svg width="56" height="52" viewBox="0 0 56 52" fill="#fff"><rect x="4" y="26" width="48" height="22"/><rect x="18" y="4" width="20" height="20" transform="rotate(-15 28 14)"/><rect x="14" y="26" width="28" height="4" fill="#f06a4a"/></svg>
  <h2>EXPERIENCED</h2>
  <p>Nemo enim ipsam voluptatem quia voluptas sit asper natur aut odit aut fugit, sed quia consequuntur magni dolores eos qui ratione voluptatem</p>
</section>
<section class="feature dark abs" style="left:406px">
  <svg width="62" height="52" viewBox="0 0 62 52" fill="#fff"><path d="M31 4 L58 16 H4 Z"/><rect x="8" y="19" width="46" height="4"/><rect x="11" y="25" width="6" height="17"/><rect x="21" y="25" width="6" height="17"/><rect x="35" y="25" width="6" height="17"/><rect x="45" y="25" width="6" height="17"/><rect x="4" y="44" width="54" height="6"/></svg>
  <h2>DEDICATED</h2>
  <p>Nemo enim ipsam voluptatem quia voluptas sit asper natur aut odit aut fugit, sed quia consequuntur magni dolores eos qui ratione voluptatem</p>
</section>
<section class="feature dark abs" style="left:803px">
  <svg width="56" height="52" viewBox="0 0 56 52" fill="#fff"><rect x="8" y="14" width="40" height="6"/><path d="M12 22 H44 L40 50 H16 Z"/><rect x="26" y="2" width="4" height="12"/></svg>
  <h2>RESPECTED</h2>
  <p>Nemo enim ipsam voluptatem quia voluptas sit asper natur aut odit aut fugit, sed quia consequuntur magni dolores eos qui ratione voluptatem</p>
</section>

<div class="portrait-frame abs"><div class="portrait" role="img" aria-label="Portrait photograph of the candidate"></div></div>

<section class="about abs">
  <h2>About Me</h2>
  <p>Evelyn was born and raised in Harbor City, the daughter of an air-conditioning repairman who later opened his own successful business. As the first in her family to go to college, her parents could not have been more proud as she finished her degree at Coastal State University, then continued on to Bayview College of Law where she graduated with honors.</p>
  <p>Dedicating her life to public service in the central region, she has spent the last 18 years as a prosecutor fighting for victims of child abuse and sexual abuse in Cedar and Willow counties. She participates in local charities such as the Harvest Table Food Bank and the Community Reading League. Evelyn shares her knowledge and experience freely, often mentoring the other young prosecutors and lecturing on jury selection and trial strategies. She is also committed to ensuring ethical behavior in the profession of law. In law school, she won an award for ethics and professionalism but since then she also served as Chair of a State Bar Grievance Committee, which handles complaints and ethical violations committed by local attorneys.</p>
  <p>The cornerstone of Evelyn's candidacy for judge is her experience in the courtroom. Nobody knows how to run an efficient courtroom better than an attorney who has litigated a hundred felony jury trials and argued more pretrial motions than can be counted. But even a judge with all the right knowledge and experience cannot excel without the correct temperament.</p>
</section>

<section class="vote-band abs" role="img" aria-label="Blue-toned background of a state flag and capitol"></section>
<div class="vote-art abs" role="img" aria-label="Photograph of raised hands holding colorful letters spelling vote"></div>
<div class="video abs" role="img" aria-label="Video player showing a crowd at a rally">
  <div class="play abs"></div>
  <div class="bar abs"><div class="track abs"><div class="fill abs"></div></div><span class="time abs">00:34</span></div>
</div>

<section class="partners abs">
  <div class="arrow abs" style="left:32px"><svg width="37" height="37" viewBox="0 0 37 37"><path d="M21 12 L15 18.5 L21 25" fill="none" stroke="#333" stroke-width="2"/></svg></div>
  <div class="badge abs" style="left:118px;width:126px"></div>
  <div class="badge abs" style="left:310px;width:100px"></div>
  <div class="badge abs" style="left:464px;width:118px"></div>
  <div class="badge abs" style="left:614px;width:144px"></div>
  <div class="badge abs" style="left:776px;width:144px"></div>
  <div class="badge abs" style="left:938px;width:146px"></div>
  <div class="arrow abs" style="left:1128px"><svg width="37" height="37" viewBox="0 0 37 37"><path d="M16 12 L22 18.5 L16 25" fill="none" stroke="#333" stroke-width="2"/></svg></div>
</section>

<section class="cta abs">
  <p class="abs">The cornerstone of Evelyn's candidacy for judge is her experience in the courtroom.</p>
  <div class="btn-donate abs">DONATE</div>
</section>

<footer class="footer abs">
  <span class="social abs" style="left:442px"></span>
  <span class="social abs" style="left:510px"></span>
  <span class="social abs" style="left:579px"></span>
  <span class="social abs" style="left:646px"></span>
  <span class="social abs" style="left:713px"></span>
  <nav class="footer-nav abs"><span>HOME</span><span class="sep">|</span><span>ABOUT</span><span class="sep">|</span><span>EVENTS</span><span class="sep">|</span><span>CONTACT</span><span class="sep">|</span><span>PRESS RELEASE</span></nav>
  <div class="rule abs"></div>
  <p class="copy abs">© 2016 Evelyn. All Rights Reserved</p>
</footer>

</body>
</html>
```